Veldmark Supplies Business Card

Professional business card that stand out to our potential customers. Front and back with clean modern design

Industry/Entity Type

Oil and gas

Contact Information for Business Card

Name, address, website , office phone and cell number

Requirements
Must have
• Editable files for each employee

```html
<!DOCTYPE html>
<html lang="en">
<head>
<meta charset="utf-8">
<title>Veldmark Supplies Business Card</title>
<link href="https://fonts.googleapis.com/css2?family=Poppins:wght@400;600&display=swap" rel="stylesheet">
<style>
  :root {
    --backdrop: #e2e6e8;
    --card-dark: #222225;
    --brand-red: #e92629;
    --brand-blue: #12b2d3;
    --ink-light: #ffffff;
  }
  * { margin: 0; padding: 0; box-sizing: border-box; }
  html, body { width: 1200px; height: 960px; overflow: hidden; }
  body {
    background: var(--backdrop);
    font-family: "Poppins", sans-serif;
    position: relative;
  }
  .card {
    position: absolute;
    width: 536px;
    height: 306px;
    overflow: hidden;
  }
  .card--front { left: 43px; background: var(--card-dark); }
  .card--back { left: 621px; }
  .card--back-blue { background: var(--brand-blue); }
  .card--back-red { background: var(--brand-red); }
  .row-top { top: 160px; }
  .row-bottom { top: 495px; }

  .front__brand {
    position: absolute;
    left: 20px;
    top: 62px;
    display: flex;
    align-items: center;
    gap: 8px;
    font-weight: 600;
    font-size: 17px;
    color: var(--brand-red);
    letter-spacing: 0.2px;
  }
  .brand-square { width: 14px; height: 14px; background: var(--brand-blue); }

  .front__accent {
    position: absolute; left: 0; top: 150px;
    width: 10px; height: 40px; background: var(--brand-red);
  }
  .front__name {
    position: absolute; left: 17px; top: 146px;
    font-size: 24px; line-height: 1.2; color: var(--brand-blue);
  }
  .front__name .first { color: var(--brand-red); font-weight: 600; }
  .front__title {
    position: absolute; left: 17px; top: 177px;
    font-size: 12.5px; color: var(--ink-light);
  }
  .front__contacts {
    position: absolute; left: 17px; top: 216px;
    list-style: none; font-size: 13px; color: var(--ink-light);
  }
  .front__contacts li {
    display: flex; align-items: center; gap: 9px;
    height: 16.5px;
  }
  .front__contacts svg { width: 11px; height: 11px; flex: none; }
  .front__divider {
    position: absolute; left: 228px; top: 220px;
    width: 2px; height: 67px; background: var(--brand-red);
  }
  .front__address {
    position: absolute; left: 255px; top: 246px;
    font-size: 13px; line-height: 1.3; color: var(--brand-red);
  }

  .back__brand {
    position: absolute; left: 0; right: 0; top: 136px;
    display: flex; justify-content: center; align-items: center; gap: 12px;
    font-weight: 600; font-size: 30px; color: var(--ink-light);
  }
  .back__brand .brand-square { width: 24px; height: 24px; background: var(--ink-light); }
</style>
</head>
<body>

  <section class="card card--front row-top">
    <div class="front__brand"><span class="brand-square"></span>Veldmark Supplies</div>
    <div class="front__accent"></div>
    <h1 class="front__name"><span class="first">Mara</span> Lindqvist</h1>
    <p class="front__title">Co-Founder &amp; CEO</p>
    <ul class="front__contacts">
      <li><svg viewBox="0 0 12 12"><path d="M2 1l2 0 1 3-1.5 1a6 6 0 0 0 3.5 3.5L8 7l3 1v2a1 1 0 0 1-1 1A9 9 0 0 1 1 2a1 1 0 0 1 1-1z" fill="var(--brand-blue)"/></svg>(432) 610-4417</li>
      <li><svg viewBox="0 0 12 12"><rect x="3" y="0.8" width="6" height="10.4" rx="1" fill="none" stroke="var(--brand-red)" stroke-width="1.3"/></svg>(432) 610-8823</li>
      <li><svg viewBox="0 0 12 12"><circle cx="6" cy="6" r="5.2" fill="var(--brand-blue)"/><path d="M1 6h10M6 1c-2 3-2 7 0 10M6 1c2 3 2 7 0 10" stroke="var(--card-dark)" stroke-width="0.8" fill="none"/></svg>www.veldmark.com</li>
      <li><svg viewBox="0 0 12 12"><rect x="1" y="3" width="10" height="7.5" fill="var(--brand-red)"/><path d="M1 3l5 4 5-4" stroke="var(--card-dark)" stroke-width="0.9" fill="none"/></svg>hello@veldmark.com</li>
    </ul>
    <div class="front__divider"></div>
    <p class="front__address">48 Ridgeline Avenue,<br>Marlow, TX 75501</p>
  </section>

  <section class="card card--back card--back-blue row-top">
    <div class="back__brand"><span class="brand-square"></span>Veldmark Supplies</div>
  </section>

  <section class="card card--front row-bottom">
    <div class="front__brand"><span class="brand-square"></span>Veldmark Supplies</div>
    <div class="front__accent"></div>
    <h1 class="front__name"><span class="first">Mara</span> Lindqvist</h1>
    <p class="front__title">Co-Founder &amp; CEO</p>
    <ul class="front__contacts">
      <li><svg viewBox="0 0 12 12"><path d="M2 1l2 0 1 3-1.5 1a6 6 0 0 0 3.5 3.5L8 7l3 1v2a1 1 0 0 1-1 1A9 9 0 0 1 1 2a1 1 0 0 1 1-1z" fill="var(--brand-blue)"/></svg>(432) 610-4417</li>
      <li><svg viewBox="0 0 12 12"><rect x="3" y="0.8" width="6" height="10.4" rx="1" fill="none" stroke="var(--brand-red)" stroke-width="1.3"/></svg>(432) 610-8823</li>
      <li><svg viewBox="0 0 12 12"><circle cx="6" cy="6" r="5.2" fill="var(--brand-blue)"/><path d="M1 6h10M6 1c-2 3-2 7 0 10M6 1c2 3 2 7 0 10" stroke="var(--card-dark)" stroke-width="0.8" fill="none"/></svg>www.veldmark.com</li>
      <li><svg viewBox="0 0 12 12"><rect x="1" y="3" width="10" height="7.5" fill="var(--brand-red)"/><path d="M1 3l5 4 5-4" stroke="var(--card-dark)" stroke-width="0.9" fill="none"/></svg>hello@veldmark.com</li>
    </ul>
    <div class="front__divider"></div>
    <p class="front__address">48 Ridgeline Avenue,<br>Marlow, TX 75501</p>
  </section>

  <section class="card card--back card--back-red row-bottom">
    <div class="back__brand"><span class="brand-square"></span>Veldmark Supplies</div>
  </section>

</body>
</html>
```